Corporate Design für logopädische Praxis
Zielgruppe
Ich gründe eine logopädische Praxis, die Sprachtherapie sowohl für Erwachsene als auch Kinder anbietet und damit ein Logo benötigt, das jede Altersgruppe anspricht und 'Lindenhof' als fachliche und menschliche Qualitätszeit interpretiert.
Aufgabenstellung
Ich bevorzuge ein klares Design, welches das Wortspiel der 'Lindenhof' im Idealfall aufgreift und den Patienten vermittelt, dass sowohl die fachliche Qualität der Behandlung als auch die Ebene von Empathie und Patientenorientierung im zwischenmenschlichen Umgang für die Praxis zentral sind.

```html
<!DOCTYPE html>
<html lang="de">
<head>
<meta charset="utf-8">
<title>Lindenhof – Corporate Design</title>
<link href="https://fonts.googleapis.com/css2?family=Montserrat:wght@300;400&family=Roboto:wght@300&display=swap" rel="stylesheet">
<style>
  :root {
    --lilac: #a48fa9;
    --rose: #c4a79f;
    --tagline: #8d8790;
    --paper: #fafafa;
    --stage: #3d3d3d;
    --ink: #3f3f3f;
    --ink-soft: #8a8a8a;
    --ink-faint: #bdbdbd;
  }
  * { box-sizing: border-box; margin: 0; padding: 0; }
  html, body { width: 1200px; height: 2760px; overflow: hidden; }
  body { position: relative; background: var(--paper); font-family: 'Montserrat', sans-serif; font-weight: 300; color: var(--ink); }

  .brand { position: absolute; display: flex; flex-direction: column; align-items: flex-end; font-family: 'Montserrat', sans-serif; font-weight: 300; white-space: nowrap; line-height: 1; }
  .brand-name { display: flex; align-items: center; gap: .3em; color: var(--lilac); }
  .brand-dot { width: .55em; height: .55em; border-radius: 50%; border: .06em solid currentColor; flex: none; }
  .brand-tagline { color: var(--tagline); letter-spacing: .16em; margin-top: .25em; }

  .hero { position: absolute; left: 0; top: 0; width: 1200px; height: 978px; background: var(--paper); }
  .hero .brand { left: 50%; top: 424px; transform: translateX(-50%); }
  .hero .brand-name { font-size: 100px; }
  .hero .brand-tagline { font-size: 31px; }

  .stage { position: absolute; left: 0; top: 978px; width: 1200px; height: 1782px; background: var(--stage); }

  .card { position: absolute; top: 57px; width: 380px; height: 245px; }
  .card-front { left: 191px; background: var(--lilac); }
  .card-front .brand { left: 50%; top: 88px; transform: translateX(-50%); }
  .card-front .brand-name { color: #fff; font-size: 42px; }
  .card-front .brand-tagline { color: #fff; font-size: 13px; }
  .card-back { left: 629px; background: #fff; }
  .card-back .brand { left: 34px; top: 36px; }
  .card-back .brand-name { font-size: 38px; }
  .card-back .brand-tagline { font-size: 12px; }
  .card-person { position: absolute; left: 34px; top: 152px; font-size: 10px; line-height: 14px; color: var(--ink-soft); }
  .card-person .name { font-size: 11px; color: var(--ink); letter-spacing: .02em; }
  .card-person .addr { margin-top: 16px; }
  .card-contacts { position: absolute; left: 208px; top: 150px; font-size: 9px; line-height: 16px; color: var(--ink-soft); list-style: none; }

  .contact-row { display: flex; align-items: center; gap: 6px; }
  .contact-icon { flex: none; border-radius: 50%; background: var(--rose); display: flex; align-items: center; justify-content: center; }
  .card-contacts .contact-icon { width: 11px; height: 11px; }
  .card-contacts svg { width: 7px; height: 7px; }

  .letter { position: absolute; left: 131px; top: 350px; width: 938px; height: 1327px; background: #fff; }
  .letter .brand { right: 68px; top: 84px; }
  .letter .brand-name { font-size: 50px; }
  .letter .brand-tagline { font-size: 16px; }
  .fold-mark { position: absolute; left: 0; width: 22px; height: 1px; background: var(--ink-soft); }
  .sender-line { position: absolute; left: 116px; top: 262px; font-size: 9px; color: var(--ink-soft); }
  .recipient { position: absolute; left: 116px; top: 284px; font-family: 'Roboto', sans-serif; font-size: 15.5px; line-height: 19px; }
  .letter-person { position: absolute; left: 699px; top: 194px; font-size: 13px; line-height: 19px; color: var(--ink-soft); }
  .letter-person .name { font-size: 16px; color: var(--ink); letter-spacing: .03em; line-height: 22px; }
  .letter-contacts { position: absolute; left: 697px; top: 299px; list-style: none; font-size: 13px; line-height: 24.5px; color: var(--ink-soft); }
  .letter-contacts .contact-icon { width: 17px; height: 17px; margin-right: 3px; }
  .letter-contacts svg { width: 10px; height: 10px; }
  .letter-body { position: absolute; left: 116px; top: 463px; width: 520px; font-family: 'Roboto', sans-serif; font-size: 15.5px; line-height: 19px; }
  .letter-body p { margin-bottom: 19px; hyphens: auto; }
  .letter-body .salutation { margin-bottom: 38px; }
  .signature { width: 150px; height: 78px; background: linear-gradient(90deg, rgba(26,54,130,.10), rgba(26,54,130,.04)); margin-top: -4px; }
  .letter-footer { position: absolute; left: 116px; top: 1252px; font-size: 9.5px; line-height: 13px; color: var(--ink-faint); }
</style>
</head>
<body>
  <section class="hero">
    <div class="brand">
      <div class="brand-name"><span class="brand-dot"></span>Lindenhof</div>
      <div class="brand-tagline">Praxis für Logopädie</div>
    </div>
  </section>

  <section class="stage">
    <div class="card card-front">
      <div class="brand">
        <div class="brand-name"><span class="brand-dot"></span>Lindenhof</div>
        <div class="brand-tagline">Praxis für Logopädie</div>
      </div>
    </div>

    <div class="card card-back">
      <div class="brand">
        <div class="brand-name"><span class="brand-dot"></span>Lindenhof</div>
        <div class="brand-tagline">Praxis für Logopädie</div>
      </div>
      <div class="card-person">
        <div class="name">JONAS ALBRECHT</div>
        <div>Geschäftsführer</div>
        <div class="addr">Ahornweg 7<br>31782 Talbrunn</div>
      </div>
      <ul class="card-contacts">
        <li class="contact-row"><span class="contact-icon"><svg viewBox="0 0 10 10"><path d="M2 1l2 2-1 1.2c.6 1.2 1.5 2.1 2.8 2.8L7 6l2 2-1.2 1.2C4.5 9 1 5.5.8 2.2z" fill="#fff"/></svg></span>+49 (0)4521 3 80 17-0</li>
        <li class="contact-row"><span class="contact-icon"><svg viewBox="0 0 10 10"><rect x="3" y="1" width="4" height="8" rx="1" fill="#fff"/></svg></span>+49 (0)4521 3 80 17-50</li>
        <li class="contact-row"><span class="contact-icon"><svg viewBox="0 0 10 10"><rect x="1.5" y="3.5" width="7" height="4.5" fill="#fff"/><rect x="3" y="1.5" width="4" height="2" fill="#fff"/></svg></span>+49 (0)171 9 42 63 18</li>
        <li class="contact-row"><span class="contact-icon"><svg viewBox="0 0 10 10"><circle cx="5" cy="5" r="3" fill="none" stroke="#fff" stroke-width="1.2"/></svg></span>info@praxis-lindenhof.de</li>
        <li class="contact-row"><span class="contact-icon"><svg viewBox="0 0 10 10"><circle cx="5" cy="5" r="3.5" fill="none" stroke="#fff"/><path d="M1.5 5h7M5 1.5v7" stroke="#fff"/></svg></span>praxis-lindenhof.de</li>
      </ul>
    </div>

    <article class="letter">
      <div class="brand">
        <div class="brand-name"><span class="brand-dot"></span>Lindenhof</div>
        <div class="brand-tagline">Praxis für Logopädie</div>
      </div>

      <div class="letter-person">
        <div class="name">JONAS ALBRECHT</div>
        <div>Geschäftsführer</div>
        <div>Ahornweg 7</div>
        <div>31782 Talbrunn</div>
      </div>
      <ul class="letter-contacts">
        <li class="contact-row"><span class="contact-icon"><svg viewBox="0 0 10 10"><path d="M2 1l2 2-1 1.2c.6 1.2 1.5 2.1 2.8 2.8L7 6l2 2-1.2 1.2C4.5 9 1 5.5.8 2.2z" fill="#fff"/></svg></span>+49 (0)4521 3 80 17-0</li>
        <li class="contact-row"><span class="contact-icon"><svg viewBox="0 0 10 10"><rect x="3" y="1" width="4" height="8" rx="1" fill="#fff"/></svg></span>+49 (0)4521 3 80 17-50</li>
        <li class="contact-row"><span class="contact-icon"><svg viewBox="0 0 10 10"><rect x="1.5" y="3.5" width="7" height="4.5" fill="#fff"/><rect x="3" y="1.5" width="4" height="2" fill="#fff"/></svg></span>+49 (0)171 9 42 63 18</li>
        <li class="contact-row"><span class="contact-icon"><svg viewBox="0 0 10 10"><circle cx="5" cy="5" r="3" fill="none" stroke="#fff" stroke-width="1.2"/></svg></span>info@praxis-lindenhof.de</li>
        <li class="contact-row"><span class="contact-icon"><svg viewBox="0 0 10 10"><circle cx="5" cy="5" r="3.5" fill="none" stroke="#fff"/><path d="M1.5 5h7M5 1.5v7" stroke="#fff"/></svg></span>praxis-lindenhof.de</li>
      </ul>

      <div class="fold-mark" style="top:469px"></div>
      <div class="fold-mark" style="top:939px"></div>

      <div class="sender-line">Praxis Lindenhof | Ahornweg 7 | 31782 Talbrunn</div>
      <div class="recipient">Jonas Albrecht<br>Birkenstr. 4<br>28465 Felden</div>

      <div class="letter-body">
        <p class="salutation">Sehr geehrte Damen und Herren,</p>
        <p>Lorem ipsum dolor sit amet, consetetur sadipscing elitr, sed diam nonumy eirmod tempor invidunt ut labore et dolore magna aliquyam erat, sed diam voluptua. At vero eos et accusam et justo duo dolores et ea rebum. Stet clita kasd gubergren, no sea takimata sanctus est Lorem ipsum dolor sit amet. Lorem ipsum dolor sit amet, consetetur sadipscing elitr, sed diam nonumy eirmod tempor invidunt ut labore et dolore magna aliquyam erat, sed diam voluptua. At vero eos et accusam et justo duo dolores et ea rebum. Stet clita kasd gubergren, no sea takimata sanctus est Lorem ipsum dolor sit amet. Lorem ipsum dolor sit amet, consetetur sadipscing elitr, sed diam nonumy eirmod tempor invidunt ut labore et dolore magna aliquyam erat, sed diam voluptua. At vero eos et accusam et justo duo dolores et ea rebum. Stet clita kasd gubergren, no sea takimata sanctus est Lorem ipsum dolor sit amet.</p>
        <p>Duis autem vel eum iriure dolor in hendrerit in vulputate velit esse molestie consequat, vel illum dolore eu feugiat nulla facilisis at vero eros et accumsan et iusto odio dignissim qui blandit praesent luptatum zzril delenit augue duis dolore te feugait nulla facilisi. Lorem ipsum dolor sit amet, consectetuer adipiscing elit, sed diam nonummy nibh euismod tincidunt ut laoreet dolore magna aliquam erat volutpat.</p>
        <p>Ut wisi enim ad minim veniam, quis nostrud exerci tation ullamcorper suscipit lobortis nisl ut aliquip ex ea commodo consequat. Duis autem vel eum iriure dolor in hendrerit in vulputate velit esse molestie consequat, vel illum dolore eu feugiat nulla facilisis at vero eros et accumsan et iusto odio dignissim qui blandit praesent luptatum zzril delenit augue duis dolore te feugait nulla facilisi.</p>
        <p style="margin-top:19px">Mit freundlichen Grüßen</p>
        <div class="signature" role="img" aria-label="Handschriftliche Unterschrift in blauer Tinte"></div>
      </div>

      <div class="letter-footer">
        Jonas Albrecht | Geschäftsführer | Ahornweg 7 | 31782 Talbrunn<br>
        Telefon +49 (0)4521 3 80 17-0 | Telefax +49 (0)4521 3 80 17-50 | Mobil +49 (0)171 9 42 63 18 | info@praxis-lindenhof.de | praxis-lindenhof.de<br>
        Nordbank IBAN DE71 2905 0300 0041 8823 57 | BIC NRDBDEFF | Amtsgericht Talbrunn HRN 308412 Gerichtsstand Talbrunn
      </div>
    </article>
  </section>
</body>
</html>
```